Tech business card design

We need an amazing business card design for our new business 'Pexla' a marketing tech startup based in Sydney, Australia. We provide an online marketplace for businesses to search and buy advertising media, connect with service providers and learn more about marketing. We wish to communicate 'cool tech', reliability and professionalism and design based around our logo.

Target Market(s)

Business Owners

Contact Information for Business Card

Name
Position
Email Address
Website
Phone Number

Font styles to use
Other font styles liked:
• Avenir & Avenir Next

Colors

Designer to choose colors to be used in the design.

```html
<!DOCTYPE html>
<html lang="en">
<head>
<meta charset="utf-8">
<title>Pexla business card</title>
<link rel="stylesheet" href="https://fonts.googleapis.com/css2?family=Nunito+Sans:wght@400;800&display=swap">
<style>
  :root {
    --stage: #d2d2d2;
    --paper: #ffffff;
    --navy: #13133a;
    --navy-soft: #232449;
    --navy-deep: #1b1c3e;
    --ink: #15163a;
  }
  * { margin: 0; padding: 0; box-sizing: border-box; }
  html, body { width: 1200px; height: 1200px; overflow: hidden; }
  body {
    background: var(--stage);
    font-family: "Nunito Sans", "Avenir Next", Avenir, sans-serif;
    color: var(--ink);
    position: relative;
  }
  .card { position: absolute; left: 171px; width: 848px; height: 484px; overflow: hidden; }
  .card-front { top: 94px; background: var(--paper); }
  .card-back { top: 612px; background: var(--paper); }

  .wordmark {
    position: absolute; font-weight: 800; line-height: 1; letter-spacing: -2px;
    color: var(--navy); white-space: nowrap;
  }
  .wordmark .tm { font-size: 16px; letter-spacing: 0; margin-left: 4px; }
  .front-wordmark { left: 228px; top: 96px; font-size: 152px; }

  .identity { position: absolute; right: 510px; top: 270px; text-align: right; white-space: nowrap; }
  .identity .name { font-weight: 800; font-size: 32px; line-height: 36px; }
  .identity .role { font-weight: 400; font-size: 29px; line-height: 32px; }

  .divider { position: absolute; left: 363px; top: 264px; width: 2px; height: 80px; background: var(--navy); }

  .contacts { position: absolute; left: 392px; top: 256px; list-style: none; white-space: nowrap; }
  .contacts li { display: flex; align-items: center; height: 32px; font-size: 26px; }
  .contacts li + li { margin-top: 0; }
  .contacts li:last-child { margin-top: 2px; }
  .contacts svg { width: 22px; height: 22px; margin-right: 18px; flex: none; }

  .front-band { position: absolute; left: 0; bottom: 0; width: 100%; height: 30px; background: var(--navy); }

  .pattern-field {
    position: absolute; left: 0; top: 0; width: 100%; height: 454px;
    background: linear-gradient(180deg, var(--navy-deep), var(--navy-soft));
  }
  .back-wordmark { left: 448px; top: 262px; font-size: 66px; color: var(--paper); letter-spacing: -1px; }
  .back-wordmark .tm { font-size: 8px; }
  .back-url {
    position: absolute; left: 0; bottom: 0; width: 100%; height: 30px;
    text-align: center; font-size: 28px; line-height: 30px;
  }
</style>
</head>
<body>
  <section class="card card-front">
    <div class="wordmark front-wordmark">pexla<span class="tm">TM</span></div>

    <div class="identity">
      <p class="name">Marcus Dale</p>
      <p class="role">Founder, Director</p>
    </div>

    <div class="divider"></div>

    <ul class="contacts">
      <li>
        <svg viewBox="0 0 24 24" aria-hidden="true"><path fill="var(--navy)" d="M6.62 10.79c1.44 2.83 3.76 5.14 6.59 6.59l2.2-2.2c.27-.27.67-.36 1.02-.24 1.12.37 2.33.57 3.57.57.55 0 1 .45 1 1V20c0 .55-.45 1-1 1-9.39 0-17-7.61-17-17 0-.55.45-1 1-1h3.5c.55 0 1 .45 1 1 0 1.25.2 2.45.57 3.57.11.35.03.74-.25 1.02l-2.2 2.2z"/></svg>
        +61 (0)400 555 018
      </li>
      <li>
        <svg viewBox="0 0 24 24" aria-hidden="true"><path fill="var(--navy)" d="M2 5h20v14H2z"/><path fill="none" stroke="#fff" stroke-width="2" d="M3 6l9 7 9-7"/></svg>
        marcus@pexlamedia.com.au
      </li>
      <li>
        <svg viewBox="0 0 24 24" aria-hidden="true"><g fill="none" stroke="var(--navy)" stroke-width="1.8"><circle cx="12" cy="12" r="10"/><ellipse cx="12" cy="12" rx="4.5" ry="10"/><path d="M2 12h20M4 7h16M4 17h16"/></g></svg>
        www.pexlamedia.com.au
      </li>
    </ul>

    <div class="front-band"></div>
  </section>

  <section class="card card-back">
    <div class="pattern-field" role="img" aria-label="Navy field with a faint repeating brand-name pattern"></div>
    <div class="wordmark back-wordmark">pexla<span class="tm">TM</span></div>
    <p class="back-url">www.pexlamedia.com.au</p>
  </section>
</body>
</html>
```